SnackOrbit!!! A Vending Machine Business Looking for an attractive website.

We are a vending machine business in Northern Michigan. We have changed our name and have rebranded our company. We would like an attractive website that shares who we are, what services we provide, the products we offer in our machines, along with a form businesses can fill out to see if they are a good fit for our company. I would like to have a Home Page, About SnackOrbit, Why Choose SnackOrbit?, Products & Services, Contact Us (With a Login Option), and a page with a questionnaire for thos interested in getting a FREE Vending Machine.

Target Market(s)

Businesses, Campgrounds, Schools, and many more in Northern Michigan

Industry/Entity Type

Vending Machines

Coding

Coded - Design and coding required

Number of Pages Required

5+ page

Requirements
Must have
• An inviting and enticing Home Page. I want to get my potential clients engaged in our website.
Nice to have
• Possibly background photos from Northern Michigan
Should not have
• A corporate feel. I do not want a boring website.

```html
<!DOCTYPE html>
<html lang="en">
<head>
<meta charset="utf-8">
<title>SnackOrbit – Crave. Vend. Repeat.</title>
<link rel="stylesheet" href="https://fonts.googleapis.com/css2?family=Syne:wght@400;500;600;700;800&display=swap">
<style>
:root{
  --green:#2b5226;
  --green-dark:#1f3f1b;
  --purple:#2d1b5c;
  --purple-deep:#221447;
  --ink:#111111;
  --text:#2a2a2a;
  --white:#ffffff;
  --line:#d9d9d9;
  --gold:#f2b01e;
  --black:#000000;
}
*{box-sizing:border-box;margin:0;padding:0}
html,body{width:1200px;height:4409px;overflow:hidden}
body{position:relative;background:var(--white);font-family:"Syne",sans-serif;color:var(--text)}
.abs{position:absolute}
.btn{position:absolute;display:flex;align-items:center;justify-content:center;font-size:13px;font-weight:500;color:var(--white);background:var(--green)}
h1,h2,h3{font-family:"Syne",sans-serif;color:var(--ink)}

/* header */
.topline{top:0;left:0;width:1200px;height:7px;background:var(--green)}
.brand{font-weight:700;font-size:26px;white-space:nowrap;color:var(--purple)}
.nav{top:60px;left:375px;display:flex;gap:20px;font-size:13px;color:#222}
.nav span{white-space:nowrap}
.user{top:60px;left:920px}
.header-btn{top:48px;left:964px;width:125px;height:48px}

/* hero */
.hero{top:125px;left:0;width:1200px;height:628px;background:linear-gradient(100deg,#8a96ab 0%,#b8c0cc 35%,#d5d7dc 55%,#9d3a3f 72%,#6b7384 88%,#c9ccd3 100%)}
.hero-shade{top:125px;left:0;width:1200px;height:628px;background:linear-gradient(90deg,rgba(20,30,60,.35),rgba(20,30,60,0) 55%)}
.hero-brand{top:318px;left:110px;font-size:54px;font-weight:700;white-space:nowrap;color:var(--white)}
.hero-title{top:416px;left:111px;font-size:38px;font-weight:700;white-space:nowrap;color:var(--white)}
.hero-sub{top:474px;left:114px;font-size:18px;font-weight:700;white-space:nowrap;color:var(--white)}
.hero-btn{top:527px;left:111px;width:120px;height:46px;background:var(--purple-deep)}

/* about */
.about-title{top:810px;left:113px;font-size:40px;font-weight:700}
.about-text{top:880px;left:114px;width:460px;font-size:13.5px;line-height:30px;color:#222}
.about-btn{top:1082px;left:115px;width:123px;height:43px}
.about-media{top:805px;left:745px;width:300px;height:360px;background:linear-gradient(135deg,#e4e4e6,#b9bcc2 45%,#2a2a2a 60%,#e1a92a 85%);border-radius:4px}

/* why */
.why{top:1250px;left:0;width:1200px;height:558px;background:linear-gradient(90deg,#3a2668 0%,#2e1c5e 50%,#3b2a6d 100%)}
.why-title{top:1310px;left:0;width:1200px;text-align:center;font-size:40px;font-weight:700;color:var(--white)}
.why-col{position:absolute;width:200px;text-align:center;color:var(--white)}
.why-col svg{display:block;margin:0 auto 20px}
.why-col h3{color:var(--white);font-size:15.5px;font-weight:700;line-height:22px;margin-bottom:10px}
.why-col p{font-size:11.5px;line-height:23px}
.why-col .arrow{margin-top:14px}

/* services */
.services-title{top:1880px;left:0;width:1200px;text-align:center;font-size:40px;font-weight:700}
.tabs{top:1970px;left:173px;display:flex;border:1px solid var(--line)}
.tab{width:171px;height:101px;border-right:1px solid var(--line);display:flex;flex-direction:column;align-items:center;justify-content:center;gap:10px;font-size:12px;color:#333}
.tab:last-child{border-right:0}
.tab.active{background:var(--green);color:var(--white)}
.service-media{top:2131px;left:257px;width:300px;height:351px;background:linear-gradient(135deg,#3a3a3c,#1b1b1d 60%,#8f2c3a 75%,#2a2a2a);border-radius:4px}
.service-title{top:2160px;left:644px;font-size:23px;font-weight:700}
.service-text{top:2203px;left:644px;width:440px;font-size:13.5px;line-height:30px;color:#222}
.service-btn{top:2393px;left:644px;width:123px;height:41px}

/* questionnaire */
.quest{top:2537px;left:0;width:1200px;height:394px;background:linear-gradient(90deg,#2f5a27,#3c6a2f 50%,#2d5725)}
.quest-title{top:2618px;left:0;width:1200px;text-align:center;font-size:40px;font-weight:700;color:var(--white)}
.quest-text{top:2697px;left:290px;width:620px;text-align:center;font-size:13.5px;line-height:30px;color:var(--white)}
.quest-btn{top:2813px;left:529px;width:125px;height:41px;background:var(--white);color:#222}

/* products */
.products-title{top:3004px;left:0;width:1200px;text-align:center;font-size:40px;font-weight:700}
.card{position:absolute;top:3099px;width:317px;height:441px;background:var(--white);box-shadow:0 2px 10px rgba(0,0,0,.12)}
.card .media{position:absolute;top:12px;left:9px;width:299px;height:330px}
.card .tools{position:absolute;top:22px;right:18px;width:28px;display:flex;flex-direction:column;gap:10px;align-items:center;background:var(--white);padding:8px 0}
.card h3{position:absolute;top:355px;left:0;width:317px;text-align:center;font-size:16px;font-weight:700;white-space:nowrap}
.card .price{position:absolute;top:390px;left:30px;font-size:13px;color:#222}
.card .stars{position:absolute;top:390px;right:30px;font-size:11px;color:var(--gold);letter-spacing:1px}
.view-btn{top:3569px;left:538px;width:123px;height:40px}

/* footer */
.footer{top:3790px;left:0;width:1200px;height:619px;background:var(--black)}
.cta-title{top:3890px;left:125px;font-size:36px;font-weight:400;line-height:48px;color:var(--white)}
.cta-text{top:3895px;left:650px;width:440px;font-size:13.5px;line-height:30px;color:var(--white)}
.foot-brand{top:4082px;left:113px;font-size:34px;font-weight:700;white-space:nowrap;color:var(--white)}
.social{top:4164px;left:114px;display:flex;gap:6px}
.social span{width:27px;height:27px;border-radius:3px;display:block}
.foot-col{position:absolute;top:4080px;color:var(--white)}
.foot-col h4{font-size:18px;font-weight:700;margin-bottom:25px}
.foot-col ul{list-style:none;font-size:12.5px}
.foot-col li{height:33px}
.contact-row{display:flex;align-items:center;gap:16px;font-size:12.5px;height:67px}
.contact-row svg{flex:none}
.foot-rule{top:4362px;left:111px;width:979px;height:1px;background:#bdbdbd}
.copy{top:4381px;left:0;width:1200px;text-align:center;font-size:11.5px;color:var(--white)}
</style>
</head>
<body>

<header>
  <div class="abs topline"></div>
  <div class="abs brand" style="top:52px;left:110px">SnackOrbit</div>
  <nav class="abs nav">
    <span>Home</span><span>About SnackOrbit</span><span>Why Choose SnackOrbit?</span><span>Products</span><span>Services</span>
  </nav>
  <svg class="abs user" width="18" height="18" viewBox="0 0 18 18" fill="none" stroke="#222" stroke-width="1.4"><circle cx="9" cy="5.5" r="3.5"/><path d="M2 17c0-4 3-6 7-6s7 2 7 6"/></svg>
  <div class="btn header-btn">Contact Us</div>
</header>

<section>
  <div class="abs hero" role="img" aria-label="Bright hallway with red and glass-front vending machines beside blue seating"></div>
  <div class="abs hero-shade"></div>
  <div class="abs hero-brand">SnackOrbit</div>
  <h1 class="abs hero-title">Crave. Vend. Repeat.</h1>
  <p class="abs hero-sub">Elevating Snacking, One Vend at a Time</p>
  <div class="btn hero-btn">Get Started</div>
  <svg class="abs" style="top:630px;left:0" width="1200" height="130" viewBox="0 0 1200 130" preserveAspectRatio="none">
    <path d="M0,38 C180,-10 300,110 520,98 C720,86 820,8 1010,40 C1100,55 1160,40 1200,20 L1200,130 L0,130 Z" fill="#2d1b5c"/>
    <path d="M0,46 C180,2 300,118 520,106 C720,94 820,18 1010,50 C1100,65 1160,50 1200,30 L1200,130 L0,130 Z" fill="#2b5226"/>
    <path d="M0,58 C180,18 300,126 520,114 C720,102 820,30 1010,62 C1100,77 1160,62 1200,42 L1200,130 L0,130 Z" fill="#ffffff"/>
  </svg>
</section>

<section>
  <h2 class="abs about-title">About SnackOrbit</h2>
  <p class="abs about-text">At SnackOrbit, we don’t just vend snacks—we curate cravings. Our customized vending solutions bring flavor, convenience, and community to Northern Michigan. Whether you’re reaching for a mid-morning snack, a refreshing beverage, or a satisfying breakfast burrito, SnackOrbit delivers delight with every bite.</p>
  <div class="btn about-btn">Read More</div>
  <div class="abs about-media" role="img" aria-label="Glass-front vending machine stocked with snacks and drinks"></div>
</section>

<section>
  <div class="abs why" role="img" aria-label="Row of vending machines in a station corridor under a purple tint"></div>
  <h2 class="abs why-title">Why Choose SnackOrbit?</h2>

  <div class="why-col" style="top:1432px;left:123px">
    <svg width="44" height="44" viewBox="0 0 44 44" fill="none" stroke="#fff" stroke-width="1.6"><path d="M26 16c-3-4-9-1-6 4l6 6 6-6c3-5-3-8-6-4z"/><path d="M6 30h8l6 3h8M6 38h20l12-8"/></svg>
    <h3>Local Love</h3>
    <p>We celebrate the heart of Michigan by partnering with local legends. Say hello to Pine Ridge Jerky and Bay Shore Crisps—our hometown heroes.</p>
    <svg class="arrow" width="20" height="12" viewBox="0 0 20 12" fill="none" stroke="#fff" stroke-width="1.5"><path d="M1 6h17M13 1l5 5-5 5"/></svg>
  </div>

  <div class="why-col" style="top:1438px;left:374px">
    <svg width="44" height="44" viewBox="0 0 44 44" fill="none" stroke="#fff" stroke-width="1.6"><circle cx="22" cy="22" r="17"/><circle cx="16" cy="18" r="2"/><circle cx="28" cy="18" r="2"/><path d="M14 26c4 5 12 5 16 0"/></svg>
    <h3>Unleash Your<br>Cravings</h3>
    <p>SnackOrbit isn’t bound by corporate ties. We’re the rebels of the vending world. Craving a bag of crispy, kettle-cooked chips? Done..</p>
    <svg class="arrow" width="20" height="12" viewBox="0 0 20 12" fill="none" stroke="#fff" stroke-width="1.5"><path d="M1 6h17M13 1l5 5-5 5"/></svg>
  </div>

  <div class="why-col" style="top:1438px;left:614px">
    <svg width="44" height="44" viewBox="0 0 44 44" fill="none" stroke="#fff" stroke-width="1.6"><path d="M22 4l5 4 6-1 1 6 5 4-3 5 3 5-5 4-1 6-6-1-5 4-5-4-6 1-1-6-5-4 3-5-3-5 5-4 1-6 6 1z"/><path d="M15 22l5 5 9-10"/></svg>
    <h3>Quality Meets<br>Convenience</h3>
    <p>Imagine this: You’re mid-meeting, and your stomach growls. Fear not! SnackOrbit’s machines offer top-notch snacks and beverages.</p>
    <svg class="arrow" width="20" height="12" viewBox="0 0 20 12" fill="none" stroke="#fff" stroke-width="1.5"><path d="M1 6h17M13 1l5 5-5 5"/></svg>
  </div>

  <div class="why-col" style="top:1438px;left:864px">
    <svg width="44" height="44" viewBox="0 0 44 44" fill="none" stroke="#fff" stroke-width="1.6"><path d="M22 5l14 5v11c0 9-6 15-14 18C14 36 8 30 8 21V10z"/><path d="M22 15c-3 4-5 7-5 9a5 5 0 0 0 10 0c0-2-2-5-5-9z"/></svg>
    <h3>Pandemic-Proof &amp;<br>Recession-Ready</h3>
    <p>Life throws curveballs, but SnackOrbit stands strong. Our vending machines are the unsung heroes of resilience. Rain or shine, they’re there, serving up joy.</p>
    <svg class="arrow" width="20" height="12" viewBox="0 0 20 12" fill="none" stroke="#fff" stroke-width="1.5"><path d="M1 6h17M13 1l5 5-5 5"/></svg>
  </div>
</section>

<section>
  <h2 class="abs services-title">Our Services</h2>
  <div class="abs tabs">
    <div class="tab active">
      <svg width="26" height="38" viewBox="0 0 26 38" fill="none" stroke="currentColor" stroke-width="1.4"><rect x="2" y="2" width="22" height="34" rx="1"/><path d="M5 8h12M5 14h12M5 20h12M5 26h12M20 8v10M5 31h16"/></svg>
      Food &amp; Snacks
    </div>
    <div class="tab">
      <svg width="26" height="38" viewBox="0 0 26 38" fill="none" stroke="currentColor" stroke-width="1.4"><rect x="2" y="2" width="22" height="34" rx="1"/><path d="M5 6h16v20H5zM5 12h16M5 19h16M8 31h10"/></svg>
      Drinks &amp; Coffee
    </div>
    <div class="tab">
      <svg width="24" height="38" viewBox="0 0 24 38" fill="none" stroke="currentColor" stroke-width="1.4"><circle cx="12" cy="10" r="8"/><path d="M6 18h12l2 18H4zM10 26h4"/></svg>
      Gumball &amp; Candy
    </div>
    <div class="tab">
      <svg width="26" height="38" viewBox="0 0 26 38" fill="none" stroke="currentColor" stroke-width="1.4"><rect x="2" y="2" width="22" height="34" rx="1"/><path d="M5 6h16M5 12h16M5 18h16v8H5zM8 31h10"/></svg>
      Cold &amp; Frozen
    </div>
    <div class="tab">
      <svg width="24" height="38" viewBox="0 0 24 38" fill="none" stroke="currentColor" stroke-width="1.4"><rect x="4" y="2" width="16" height="24" rx="1"/><path d="M8 7h8M8 12h8M8 17h8M12 26v10M6 36h12"/></svg>
      Custom Machines
    </div>
  </div>
  <div class="abs service-media" role="img" aria-label="Black snack vending machine with colourful product rows"></div>
  <h3 class="abs service-title">Food &amp; Snacks</h3>
  <p class="abs service-text">Lorem ipsum dolor sit amet, consectetur adipiscing elit, sed do eiusmod tempor incididunt ut labore et dolore magna aliqua. Ut enim ad minim veniam, quis nostrud exercitation ullamco laboris nisi ut aliquip ex ea commodo consequat. Duis aute irure dolor in reprehenderit in voluptate velit esse cillum dolore eu fugiat nulla pariatur.</p>
  <div class="btn service-btn">Read More</div>
</section>

<section>
  <div class="abs quest" role="img" aria-label="Vending machines in a shop under a green tint"></div>
  <h2 class="abs quest-title">Get a questionnaire</h2>
  <p class="abs quest-text">Lorem ipsum dolor sit amet, consectetur adipiscing elit, sed do eiusmod tempor incididunt ut labore et dolore magna aliqua. Ut enim ad minim veniam, quis nostrud exercitation ullamco laboris nisi ut aliquip ex ea commodo consequat.</p>
  <div class="btn quest-btn">Click Here</div>
</section>

<section>
  <h2 class="abs products-title">Our Products</h2>

  <article class="card" style="left:111px">
    <div class="media" role="img" aria-label="Lit beverage vending machine beside a stone wall" style="background:linear-gradient(135deg,#3b3530,#1d2d45 45%,#3f6fa6 60%,#7a5a3a)"></div>
    <div class="tools">
      <svg width="14" height="13" viewBox="0 0 14 13" fill="none" stroke="#333" stroke-width="1.2"><path d="M7 12L1.5 6.5a3 3 0 0 1 5.5-4 3 3 0 0 1 5.5 4z"/></svg>
      <svg width="14" height="10" viewBox="0 0 14 10" fill="none" stroke="#333" stroke-width="1.2"><path d="M1 5s2.5-4 6-4 6 4 6 4-2.5 4-6 4-6-4-6-4z"/><circle cx="7" cy="5" r="1.8"/></svg>
      <svg width="14" height="13" viewBox="0 0 14 13" fill="none" stroke="#333" stroke-width="1.2"><path d="M1 1h2l2 8h7l1-6H4"/><circle cx="6" cy="11.5" r="1"/><circle cx="11" cy="11.5" r="1"/></svg>
    </div>
    <h3>Beverages Vending Machines</h3>
    <span class="price">$150.00</span><span class="stars">★★★★★</span>
  </article>

  <article class="card" style="left:442px">
    <div class="media" role="img" aria-label="Snack vending machine with stocked spiral rows" style="background:linear-gradient(135deg,#2c2c2c,#8b8478 40%,#b04a3a 60%,#3a3a3a)"></div>
    <div class="tools">
      <svg width="14" height="13" viewBox="0 0 14 13" fill="none" stroke="#333" stroke-width="1.2"><path d="M7 12L1.5 6.5a3 3 0 0 1 5.5-4 3 3 0 0 1 5.5 4z"/></svg>
      <svg width="14" height="10" viewBox="0 0 14 10" fill="none" stroke="#333" stroke-width="1.2"><path d="M1 5s2.5-4 6-4 6 4 6 4-2.5 4-6 4-6-4-6-4z"/><circle cx="7" cy="5" r="1.8"/></svg>
      <svg width="14" height="13" viewBox="0 0 14 13" fill="none" stroke="#333" stroke-width="1.2"><path d="M1 1h2l2 8h7l1-6H4"/><circle cx="6" cy="11.5" r="1"/><circle cx="11" cy="11.5" r="1"/></svg>
    </div>
    <h3>Snacks Vending Machines</h3>
    <span class="price">$450.00</span><span class="stars">★★★★★</span>
  </article>

  <article class="card" style="left:772px">
    <div class="media" role="img" aria-label="Close view of chocolate bars and chip bags on vending spirals" style="background:linear-gradient(135deg,#5a3a6e,#c7452f 35%,#e2b23a 55%,#2e4d8a 80%,#3b3b3b)"></div>
    <div class="tools">
      <svg width="14" height="13" viewBox="0 0 14 13" fill="none" stroke="#333" stroke-width="1.2"><path d="M7 12L1.5 6.5a3 3 0 0 1 5.5-4 3 3 0 0 1 5.5 4z"/></svg>
      <svg width="14" height="10" viewBox="0 0 14 10" fill="none" stroke="#333" stroke-width="1.2"><path d="M1 5s2.5-4 6-4 6 4 6 4-2.5 4-6 4-6-4-6-4z"/><circle cx="7" cy="5" r="1.8"/></svg>
      <svg width="14" height="13" viewBox="0 0 14 13" fill="none" stroke="#333" stroke-width="1.2"><path d="M1 1h2l2 8h7l1-6H4"/><circle cx="6" cy="11.5" r="1"/><circle cx="11" cy="11.5" r="1"/></svg>
    </div>
    <h3>Chocolates Vending Machine</h3>
    <span class="price">$350.00</span><span class="stars">★★★★★</span>
  </article>

  <div class="btn view-btn">View All</div>
</section>

<footer>
  <svg class="abs" style="top:3690px;left:0" width="1200" height="110" viewBox="0 0 1200 110" preserveAspectRatio="none">
    <path d="M0,60 C160,110 260,0 440,20 C600,40 640,90 820,70 C980,52 1060,0 1200,30 L1200,110 L0,110 Z" fill="#2d1b5c"/>
    <path d="M0,70 C160,120 260,10 440,30 C600,50 640,100 820,80 C980,62 1060,10 1200,40 L1200,110 L0,110 Z" fill="#2b5226"/>
    <path d="M0,80 C160,128 260,20 440,40 C600,60 640,108 820,90 C980,72 1060,20 1200,50 L1200,110 L0,110 Z" fill="#ffffff"/>
    <path d="M0,86 C160,134 260,26 440,46 C600,66 640,114 820,96 C980,78 1060,26 1200,56 L1200,110 L0,110 Z" fill="#000000"/>
  </svg>
  <div class="abs footer"></div>

  <h2 class="abs cta-title">Ready to experience the<br>SnackOrbit difference?</h2>
  <p class="abs cta-text">Sign up now and let’s connect. Taste the future of snacking firsthand! Contact us today and explore how our vending magic can elevate your space</p>

  <div class="abs foot-brand">SnackOrbit</div>
  <div class="abs social">
    <span style="background:#1877f2"></span>
    <span style="background:#ffffff"></span>
    <span style="background:#e60023"></span>
    <span style="background:#c13584"></span>
    <span style="background:#ff0000"></span>
  </div>

  <div class="foot-col" style="left:430px">
    <h4>Quick Links</h4>
    <ul><li>Home</li><li>About SnackOrbit</li><li>Why Choose SnackOrbit?</li><li>Products</li><li>Services</li><li>Contact Us</li></ul>
  </div>

  <div class="foot-col" style="left:663px">
    <h4>Contact Info</h4>
    <div class="contact-row" style="height:54px;margin-top:-12px">
      <svg width="26" height="26" viewBox="0 0 26 26"><rect width="26" height="26" rx="4" fill="#fff"/><path d="M13 5a5 5 0 0 0-5 5c0 4 5 10 5 10s5-6 5-10a5 5 0 0 0-5-5z" fill="#000"/><circle cx="13" cy="10" r="2" fill="#fff"/></svg>
      Lorem Ipsum,Usa - 437916
    </div>
    <div class="contact-row">
      <svg width="26" height="26" viewBox="0 0 26 26"><rect width="26" height="26" rx="4" fill="#fff"/><path d="M8 6l3 0 1 4-2 1c1 2 3 4 5 5l1-2 4 1v3c-6 1-13-6-12-12z" fill="#000"/></svg>
      +1 888 888 8888
    </div>
    <div class="contact-row">
      <svg width="26" height="26" viewBox="0 0 26 26"><rect width="26" height="26" rx="4" fill="#fff"/><rect x="6" y="8" width="14" height="10" fill="none" stroke="#000" stroke-width="1.5"/><path d="M6 8l7 6 7-6" fill="none" stroke="#000" stroke-width="1.5"/></svg>
      info@snackorbit
    </div>
  </div>

  <div class="foot-col" style="left:957px">
    <h4>Help Links</h4>
    <ul><li>Privay Policy</li><li>Terms &amp; Conditions</li></ul>
  </div>

  <div class="abs foot-rule"></div>
  <p class="abs copy">Copyright © 2024 SnackOrbit. All rights reserved.</p>
</footer>

</body>
</html>
```